Oil and Gas Construction Company Brochure Design

We're redesigning our company Brochure. The easiest part about this...the layout, content, photos, etc. will follow our newly redesigned website:

www.brelvanworks.com

Thank you very much and please contact me should you have any questions!

Target Market(s)

Engineers, management, and operators in the oil field services

Industry/Entity Type

Oil And Gas

Requirements
Must have
• The same layout as the website, the same content, the same photos (ask me if you need anymore photos or if the layout your chose needs more)
• Also, follow the same color scheme as the website. Follow the same feel/mood as the website. Follow the same text as the website.

```html
<!DOCTYPE html>
<html lang="en">
<head>
<meta charset="utf-8">
<title>Brelvan Works – Health Safety &amp; Environmental</title>
<link href="https://fonts.googleapis.com/css2?family=Oswald:wght@500;600&family=Roboto:wght@400;700&display=swap" rel="stylesheet">
<style>
  :root{
    --maroon:#7b1e2c;
    --maroon-deep:#5e1420;
    --ink:#3a3a3a;
    --paper:#ffffff;
    --footer-top:#f4f4f4;
    --footer-bottom:#d9d9d9;
    --backdrop:#b7b5b0;
  }
  *{box-sizing:border-box;margin:0;padding:0}
  html,body{width:1200px;height:1000px;overflow:hidden;background:var(--backdrop)}
  body{font-family:"Roboto",sans-serif;position:relative}
  .spread{position:absolute;left:20px;top:295px;width:1160px;height:420px;display:flex}
  .page{position:relative;width:580px;height:420px;background:var(--paper);overflow:hidden}
  .page-footer{position:absolute;left:0;right:0;bottom:0;height:62px;
    background:linear-gradient(var(--footer-top),var(--footer-bottom));
    display:flex;align-items:center;justify-content:space-between;padding:0 28px}
  .page--right .page-footer{border-top:6px solid var(--maroon)}
  .brand{display:flex;align-items:center;gap:7px;font-family:"Oswald",sans-serif;font-weight:600;
    font-size:15px;color:var(--maroon);letter-spacing:.5px}
  .brand-dot{width:20px;height:20px;border-radius:50%;background:var(--maroon)}
  .web{font-size:9.5px;font-weight:700;color:var(--ink)}
  /* left page */
  .intro-panel{position:absolute;left:0;top:0;width:274px;height:358px;background:var(--maroon);
    padding:68px 24px 0 26px;color:#fff}
  .intro-title{font-family:"Oswald",sans-serif;font-weight:500;font-size:27px;line-height:1.02;
    text-transform:uppercase;border-left:2px solid #fff;padding-left:6px;margin-bottom:22px}
  .intro-panel p{font-size:7.4px;line-height:1.5;margin-bottom:10px;text-align:justify}
  .photo-site{position:absolute;left:274px;top:0;width:306px;height:358px;
    background:linear-gradient(180deg,#e8eaec 0%,#b9a48f 18%,#b66a3e 45%,#9a5431 75%,#7d5a48 100%)}
  /* right page */
  .photo-plant{position:absolute;left:0;top:0;width:330px;height:352px;
    background:linear-gradient(180deg,#6f9fd4 0%,#c7d3df 35%,#8d9196 60%,#5c5f63 100%)}
  .text-panel{position:absolute;left:300px;top:0;width:280px;height:352px;
    background:linear-gradient(90deg,rgba(255,255,255,0) 0%,rgba(240,240,240,.95) 14%,#ececec 100%);
    padding:58px 24px 0 48px;color:var(--ink)}
  .text-panel p{font-size:7.4px;line-height:1.5;margin-bottom:10px}
</style>
</head>
<body>
  <main class="spread">
    <section class="page page--left">
      <div class="intro-panel">
        <h1 class="intro-title">Health Safety,<br>&amp; Environmental</h1>
        <p>Brelvan Works' success is a direct result of our commitment to providing an "Injury Free" work environment where we operate all of our facilities and projects in a safe and efficient manner, and in compliance with all applicable health, safety and environmental regulations. Our goal is to provide a work environment where facilities and projects are free of recognized hazards; and people, equipment and the environment are not placed at risk of injury or damage.</p>
        <p>Brelvan's employees are our most vital asset. We care about every individual's safety and health. While quality and productivity are critical to our operations, they will never take precedence over the safety of personnel or protection of the environment.</p>
      </div>
      <div class="photo-site" role="img" aria-label="Crew placing rebar in a foundation trench at a steel-frame construction site"></div>
      <footer class="page-footer">
        <span class="brand"><span class="brand-dot"></span>BRELVAN</span>
        <span class="web">www.brelvanworks.com</span>
      </footer>
    </section>
    <section class="page page--right">
      <div class="photo-plant" role="img" aria-label="Grey process piping and vessels at a gas facility under a blue sky"></div>
      <div class="text-panel">
        <p>Our management team holds itself responsible for recognizing, anticipating and analyzing the known and potential hazards of each project and to provide education, personal protective equipment (PPE) and leadership to eliminate those hazards and conditions at all construction sites. Our Health, Safety and Environmental Manual serves as an excellent tool for accident prevention.</p>
        <p>All Brelvan employees are trained to look for unsafe practices and conditions and correct the situation before it becomes a safety hazard. If an unsafe or hazardous condition arises during any work process, all Brelvan employees are empowered and encouraged to "stop work". Proper training, coupled with continuous communication between management and supervision ensures our capability to provide a safe working environment.</p>
        <p>Brelvan works closely with our customers to share awareness of one another's safety policies and procedures to maintain safety for all. All Brelvan employees are expected to follow these policies and procedures as well as provide input on how to improve them.</p>
        <p>Safety is a priority for all Brelvan employees whether they are on or off the job site.</p>
      </div>
      <footer class="page-footer">
        <span class="web">www.brelvanworks.com</span>
        <span class="brand"><span class="brand-dot"></span>BRELVAN</span>
      </footer>
    </section>
  </main>
</body>
</html>
```